Counseling Practice Business Card

I need a professional looking business card incorporating my new logo that was just completed. Card needs to incorporate my name and title, description of my specialty, my address, my phone number, my fax number, my email and my website URL. I need to be able to choose design on/with different paper colors and textures.
I do not have a lot of business card ideas so I am open to anything but I want bold,sharp, clear card without additional designs other than my logo (see attached file info). I am open to different color backgrounds or paper colors including black. I do not like traditional brackets around area codes in phone number or dashes between numbers in phone number. Am open to other ways of presenting including periods between numbers as appropriate. I do not know enough to know what I like yet but I want card to coordinate and work together with my logo. My practice emphasizes natural mental health interventions so any use of color (with background paper color or the blue and green in my logo) that elicits nature is nice. In addition to black, any natural brown or wood looking background might be desirable also. Most of the offerings so far look very similar and boring.

Target Market(s)

Potential therapy clients and other professionals

Contact Information for Business Card

Card information:
Gerald M. Whitcombe, Ph.D.
Licensed Clinical Psychologist
Integrative Health Coach
4812 Marlowe Ridge Blvd SE
Suite 310
Duluth, GA 30096
(770) 415-2983 phone
(770) 581-4096 fax
drgeraldwhitcombe@quillmarsh.net
brightfernwellness.net

Font styles to use
Serif
Sans Serif
Other font styles liked:
• anything that you think looks crisp, clear and easily readable

Requirements
Must have
• Any color used should coordinate with my logo design (see attached files).
• Card should be printed horizontally so top and bottom are longest sides of rectangle.
• Background color or paper color should complement and highlight logo. Do not like a white background. black, grey, brown or any color my logo would blend well with.
Nice to have
• I would like designer to utilize color to highlight letters/name or phone-fax-web symbols.
• Bottom edge of card could be highlighted if appropriate to an idea.
Should not have
• I would NOT want the card to have a pure white background at all.
• No clear cards.
• Cards should be oriented with long sides on bottom and top, NOT sides. DO NOT LIKE THIS THIN TALL ORIENTATION.

```html
<!DOCTYPE html>
<html lang="en">
<head>
<meta charset="utf-8">
<title>Brightfern Wellness – Business Card</title>
<link rel="stylesheet" href="https://fonts.googleapis.com/css2?family=Open+Sans:wght@400;600;700&family=Oswald:wght@500&display=swap">
<style>
  :root {
    --backdrop: #e2d6cb;
    --card: #a57b61;
    --card-edge: #8f6750;
    --brand-blue: #2a7cc4;
    --brand-green: #17763a;
    --ink: #2b1e17;
    --rule: #3a2c24;
  }
  * { margin: 0; padding: 0; box-sizing: border-box; }
  html, body { width: 1200px; height: 794px; overflow: hidden; background: var(--backdrop); }
  body { position: relative; font-family: "Open Sans", sans-serif; color: var(--ink); }

  .card {
    position: absolute;
    width: 600px; height: 343px;
    background: var(--card);
    border-bottom: 3px solid var(--card-edge);
    box-shadow: 0 4px 10px rgba(60, 40, 30, 0.18);
  }
  .card-front { left: 110px; top: 48px; }
  .card-back  { left: 490px; top: 404px; }

  .brand {
    display: flex; align-items: center; gap: 12px;
    font-family: "Open Sans", sans-serif; font-weight: 700;
    color: var(--brand-blue); white-space: nowrap;
  }
  .brand-dot { width: 18px; height: 18px; border-radius: 50%; background: var(--brand-green); flex: none; }
  .card-front .brand {
    position: absolute; left: 50%; top: 50%; transform: translate(-50%, -50%);
    font-size: 44px; letter-spacing: 0.5px;
  }
  .card-front .brand-dot { width: 26px; height: 26px; }

  .card-back .brand { position: absolute; left: 40px; top: 118px; font-size: 30px; }

  .identity { position: absolute; right: 34px; top: 30px; text-align: right; }
  .identity .name {
    font-family: "Oswald", sans-serif; font-weight: 500; font-size: 19px;
    color: var(--brand-blue); text-transform: uppercase; letter-spacing: 0.3px;
  }
  .identity .role { font-size: 14px; font-weight: 600; color: var(--brand-green); line-height: 1.25; }

  .rule { position: absolute; height: 2px; background: var(--rule); }
  .rule-top { left: 200px; right: 30px; top: 104px; }
  .rule-logo { left: 40px; width: 330px; top: 176px; }

  .contacts { position: absolute; left: 40px; bottom: 22px; list-style: none; font-size: 14px; line-height: 1.45; }
  .contacts li { display: flex; align-items: center; gap: 9px; }
  .contacts svg { width: 13px; height: 13px; fill: var(--brand-blue); flex: none; }

  .address { position: absolute; right: 34px; top: 196px; text-align: right; font-size: 14px; line-height: 1.35; font-weight: 600; }
</style>
</head>
<body>
  <section class="card card-front" aria-label="Card front">
    <div class="brand"><span class="brand-dot"></span>Brightfern Wellness</div>
  </section>

  <section class="card card-back" aria-label="Card back">
    <div class="identity">
      <p class="name">Gerald M. Whitcombe, Ph.D.</p>
      <p class="role">Licensed Clinical Psychologist</p>
      <p class="role">Integrative Health Coach</p>
    </div>
    <div class="rule rule-top"></div>

    <div class="brand"><span class="brand-dot"></span>Brightfern Wellness</div>
    <div class="rule rule-logo"></div>

    <address class="address">
      4812 Marlowe Ridge Blvd SE<br>
      Suite 310<br>
      Duluth, GA 30096
    </address>

    <ul class="contacts">
      <li><svg viewBox="0 0 16 16" aria-label="Phone"><path d="M3 1h3l1.5 4-2 1.3a9 9 0 0 0 4.2 4.2L11 8.5l4 1.5v3a2 2 0 0 1-2 2A12 12 0 0 1 1 3a2 2 0 0 1 2-2z"/></svg>(770) 415-2983</li>
      <li><svg viewBox="0 0 16 16" aria-label="Fax"><path d="M4 1h7v4H4zM1 6h14v7h-3v2H4v-2H1zm4 5v3h6v-3z"/></svg>(770) 581-4096</li>
      <li><svg viewBox="0 0 16 16" aria-label="Email"><path d="M1 3h14v10H1zm1.5 1.5L8 9l5.5-4.5z"/></svg>drgeraldwhitcombe@quillmarsh.net</li>
      <li><svg viewBox="0 0 16 16" aria-label="Website"><circle cx="8" cy="8" r="7"/></svg>www.brightfernwellness.net</li>
    </ul>
  </section>
</body>
</html>
```